Sophisticated, clean website reflecting my feminine, playful side to sell my abstract art,

I need a website no more than 3 pages to showcase my paintings, a little about me and some contact info. I do abstracts so looking for something a little edgy, yet feminine and current.
Updates

Hi there, These are some artists websites that I Iike: Marnelvoss.com (I like how airy it is) peterwallombry.com garethpolvens.com (I like how it scrolls) I'll need a place for a photo ( a headshot-i do not have it yet so I'll need to be able to upload that later) as well as an area for my bio. Also, it's important that I will be able to upload any new photos and descriptions easily so it should be user friendly. Lastly, I like in a sunny place so would like to have this seem upbeat and playful as that is how i like to paint. thanks-I'm trying to upload my photos now -

Target Market(s)

ppl ages 35-70 who want large scale art for their homes

Industry/Entity Type

art

Coding

Coded - Design and coding required

Number of Pages Required

3 page

Colors

Designer to choose colors to be used in the design.

Requirements
Must have
• photos of my art, a place for my bio, be easy to reach me. tasteful-nothing too "in your face" -my clients are pretty high end and organized. They like clean lines
Nice to have
• sophisticated background, muted tones in the back-similar clean font throughout-no cursive
Should not have
• too many dark areas. Too many blocks of color. Too serious.

```html
<!DOCTYPE html>
<html lang="en">
<head>
<meta charset="utf-8">
<title>Artist Gallery</title>
<link href="https://fonts.googleapis.com/css2?family=Cinzel:wght@600&family=Montserrat:wght@400;500&family=Raleway:wght@400&display=swap" rel="stylesheet">
<style>
  :root {
    --ink: #111111;
    --paper: #ffffff;
    --cream: #fff5e6;
    --gold: #e6d896;
    --gold-soft: rgba(232, 220, 160, 0.85);
    --gold-link: #e2c96e;
    --rule: #b9b9b9;
    --shadow: rgba(0, 0, 0, 0.25);
  }
  * { box-sizing: border-box; margin: 0; padding: 0; }
  html, body { width: 1200px; height: 2341px; overflow: hidden; background: var(--paper); }
  body { position: relative; font-family: "Montserrat", Arial, sans-serif; color: var(--ink); }

  .site-logo {
    position: absolute; left: 545px; top: 16px; width: 110px; height: 28px;
    border: 1px solid var(--ink); font-weight: 500; font-size: 14px;
    display: flex; align-items: center; justify-content: center; letter-spacing: 0.2px;
  }

  .main-nav { position: absolute; left: 0; top: 63px; width: 1200px; height: 43px; background: var(--cream); }
  .main-nav a {
    position: absolute; top: 10px; height: 23px; line-height: 21px; font-size: 14px;
    color: var(--ink); text-decoration: none; white-space: nowrap;
  }
  .main-nav a.is-active { border: 1px solid var(--ink); border-radius: 2px; padding: 0 7px; left: 163px; width: 135px; }

  .art-fill { position: absolute; }

  .hero { left: 0; top: 106px; width: 1200px; height: 635px;
    background: radial-gradient(circle at 70% 45%, #d9a63a 0%, #2c4f9a 22%, #e9e6de 40%, transparent 55%),
                radial-gradient(circle at 12% 62%, #c97a3a 0%, #d7a52c 20%, #e7e4dc 42%),
                #e7e4dc; }
  .hero-arrow { position: absolute; top: 413px; width: 41px; height: 39px; background: rgba(40,40,40,0.75); }
  .hero-arrow svg { position: absolute; left: 13px; top: 12px; }

  .feature { position: absolute; left: 163px; top: 863px; width: 874px; height: 492px;
    border: 3px solid var(--paper); box-shadow: 0 0 4px var(--shadow); overflow: hidden; }
  .feature .art-fill { inset: 0;
    background: linear-gradient(90deg, #8696b8 0%, #8696b8 23%, #d8cdb8 24%, #d8cdb8 37%, #0e8a7e 38%, #0b7f74 71%, #d8cdb8 72%, #d8cdb8 86%, #1b2f66 87%, #182a5c 100%); }
  .feature-caption { position: absolute; left: 0; bottom: 0; width: 100%; height: 64px; background: var(--gold-soft);
    font-family: "Cinzel", Georgia, serif; font-weight: 600; font-size: 40px; line-height: 64px; text-align: center; }

  .pager-btn { position: absolute; width: 36px; height: 25px; display: flex; align-items: center; justify-content: center; }
  .pager-btn.light { background: var(--paper); }
  .pager-btn.dark { background: var(--ink); }
  .pager-btn.gold { background: var(--gold); }

  .section-title { position: absolute; left: 0; top: 1462px; width: 1200px; text-align: center;
    font-family: "Cinzel", Georgia, serif; font-weight: 600; font-size: 42px; }
  .title-rule { position: absolute; left: 530px; top: 1521px; width: 140px; height: 1px; background: var(--rule); }
  .title-rule::after { content: ""; position: absolute; left: 63px; top: -1px; width: 14px; height: 2px; background: var(--ink); }

  .portfolio-tile { position: absolute; box-shadow: 1px 2px 4px var(--shadow); }

  .site-footer .footer-rule { position: absolute; top: 2297px; height: 1px; background: var(--rule); }
  .to-top { position: absolute; left: 591px; top: 2289px; width: 17px; height: 17px; border-radius: 50%; background: var(--gold); }
  .to-top svg { position: absolute; left: 4px; top: 4px; }
  .copyright { position: absolute; left: 163px; top: 2311px; font-family: "Raleway", Arial, sans-serif; font-size: 11.5px; }
  .copyright a { color: var(--gold-link); text-decoration: none; margin-left: 10px; }
  .social { position: absolute; top: 2307px; width: 23px; height: 23px; }
  .social.dark { left: 983px; background: var(--ink); }
  .social.gold { left: 1014px; background: var(--gold); }
</style>
</head>
<body>

<header>
  <div class="site-logo">ARTIST LOGO</div>
  <nav class="main-nav">
    <a class="is-active" href="#">Originals For Sale</a>
    <a href="#" style="left:395px">Print For Sale</a>
    <a href="#" style="left:591px">Events</a>
    <a href="#" style="left:741px">Past Work</a>
    <a href="#" style="left:917px">About The Artist</a>
  </nav>
</header>

<section class="hero-slider">
  <div class="art-fill hero" role="img" aria-label="Abstract painting with swirling gold, blue and orange brushstrokes"></div>
  <span class="hero-arrow" style="left:0;top:413px">
    <svg width="14" height="15"><polygon points="12,0 12,15 0,7.5" fill="#fff"/></svg>
  </span>
  <span class="hero-arrow" style="left:1159px;top:413px">
    <svg width="14" height="15"><polygon points="2,0 2,15 14,7.5" fill="#fff"/></svg>
  </span>
</section>

<section class="feature">
  <div class="art-fill" role="img" aria-label="Abstract painting in vertical bands of slate blue, sand, teal and navy"></div>
  <p class="feature-caption">Create Your Own Galery Today!</p>
</section>
<span class="pager-btn light" style="left:989px;top:1243px"><svg width="9" height="11"><polygon points="9,0 9,11 0,5.5" fill="#111"/></svg></span>
<span class="pager-btn gold" style="left:1045px;top:1243px"><svg width="9" height="11"><polygon points="0,0 0,11 9,5.5" fill="#fff"/></svg></span>

<section class="portfolio">
  <h2 class="section-title">Our Portfolio</h2>
  <div class="title-rule"></div>

  <div class="art-fill portfolio-tile" style="left:163px;top:1568px;width:418px;height:169px;background:linear-gradient(110deg,#5a2a26,#d9c7c2 45%,#e4b4a8 80%,#eae6e4)" role="img" aria-label="Abstract painting in deep maroon and blush pink"></div>
  <div class="art-fill portfolio-tile" style="left:618px;top:1568px;width:419px;height:169px;background:linear-gradient(100deg,#4b3a66,#7d5ba6 35%,#b9a7c4 60%,#e6dccb)" role="img" aria-label="Abstract painting in violet and lavender florals on cream"></div>
  <div class="art-fill portfolio-tile" style="left:163px;top:1769px;width:418px;height:168px;background:linear-gradient(110deg,#5e9b5a,#2f8f4a 40%,#9ccf8a 70%,#5c7a4c)" role="img" aria-label="Abstract painting in layered greens with a dark blue arc"></div>
  <div class="art-fill portfolio-tile" style="left:163px;top:1969px;width:418px;height:168px;background:linear-gradient(110deg,#2f7f80,#3a3a36 40%,#dcd8cc 60%,#2f7a66)" role="img" aria-label="Abstract painting with dark radiating strokes on teal"></div>
  <div class="art-fill portfolio-tile" style="left:618px;top:1769px;width:419px;height:368px;background:radial-gradient(circle at 48% 45%,#1f4f7a 0%,#d8a02a 28%,#c8862a 55%,#e4e0d4 85%)" role="img" aria-label="Abstract painting with a golden swirl and blue accents"></div>
</section>
<span class="pager-btn dark" style="left:958px;top:2169px"><svg width="9" height="11"><polygon points="9,0 9,11 0,5.5" fill="#fff"/></svg></span>
<span class="pager-btn gold" style="left:1002px;top:2169px"><svg width="9" height="11"><polygon points="0,0 0,11 9,5.5" fill="#fff"/></svg></span>

<footer class="site-footer">
  <div class="footer-rule" style="left:163px;width:424px"></div>
  <div class="footer-rule" style="left:613px;width:424px"></div>
  <a class="to-top" href="#" aria-label="Back to top"><svg width="9" height="7"><polygon points="0,7 9,7 4.5,0" fill="#fff"/></svg></a>
  <p class="copyright">© Copyright 2022. Artist All rights reserved. &nbsp; | <a href="#">Privacy Policy</a></p>
  <a class="social dark" href="#" aria-label="Social profile"></a>
  <a class="social gold" href="#" aria-label="Photo profile"></a>
</footer>

</body>
</html>
```